Business Card For Halvenmoor Financial Consulting

Hi, I would like a business card designed. Bold, modern.
Please use the same design as the logo. I have also attached the website design to see the overall theme.
Wordmark Font
Color: Hex: #01AEF7

```html
<!DOCTYPE html>
<html lang="en">
<head>
<meta charset="utf-8">
<title>Halvenmoor Consulting Business Card</title>
<link rel="stylesheet" href="https://fonts.googleapis.com/css2?family=Montserrat:wght@500;800&family=Open+Sans:wght@400;700&display=swap">
<style>
  :root {
    --navy: #0a3d66;
    --sky: #01aef7;
    --sky-soft: #35a7df;
    --ink: #2b2b2b;
    --paper: #ffffff;
    --backdrop: #e9e9e7;
  }
  * { box-sizing: border-box; margin: 0; padding: 0; }
  html, body { width: 1200px; height: 801px; overflow: hidden; }
  body {
    background: var(--backdrop);
    font-family: "Open Sans", sans-serif;
    position: relative;
  }
  .card {
    position: absolute;
    top: 255px;
    width: 525px;
    height: 300px;
    background: var(--paper);
    border-bottom: 4px solid var(--sky-soft);
    box-shadow: 0 10px 30px rgba(0,0,0,0.18);
    overflow: hidden;
  }
  .card--front { left: 50px; }
  .card--back { left: 625px; }

  .brand { display: flex; align-items: center; gap: 12px; }
  .brand__square {
    border: 4px solid var(--sky-soft);
    flex: none;
  }
  .brand__text { display: flex; flex-direction: column; }
  .brand__name {
    font-family: "Montserrat", sans-serif;
    font-weight: 800;
    color: var(--navy);
    line-height: 1;
  }
  .brand__tag {
    font-family: "Montserrat", sans-serif;
    font-weight: 500;
    color: var(--sky-soft);
    line-height: 1;
  }

  .card--front .brand { position: absolute; left: 34px; top: 116px; }
  .card--front .brand__square { width: 42px; height: 42px; border-width: 3px; }
  .card--front .brand__name { font-size: 30px; letter-spacing: 1px; }
  .card--front .brand__tag { font-size: 10px; letter-spacing: 13.5px; margin-top: 6px; }

  .accent-bar {
    position: absolute; top: 0; right: 22px;
    width: 34px; height: 9px; background: var(--sky-soft);
  }
  .person { position: absolute; top: 26px; right: 70px; text-align: right; }
  .person__name {
    font-weight: 700; font-size: 17px; color: var(--sky-soft); letter-spacing: 0.5px;
  }
  .person__role { font-size: 12px; color: var(--ink); }

  .feature-square {
    position: absolute; right: 34px; top: 96px;
    width: 150px; height: 150px;
    border: 9px solid var(--sky-soft);
  }

  .contact { position: absolute; left: 150px; top: 196px; color: var(--ink); }
  .contact__address { font-size: 12px; line-height: 1.35; margin-bottom: 6px; }
  .contact__line { display: flex; align-items: center; gap: 6px; font-size: 12px; line-height: 1.4; }
  .contact__line svg { width: 10px; height: 10px; fill: var(--sky-soft); flex: none; }

  .card--back .brand { position: absolute; left: 50%; top: 50%; transform: translate(-50%, -50%); gap: 16px; }
  .card--back .brand__square { width: 68px; height: 68px; border-width: 5px; }
  .card--back .brand__name { font-size: 44px; letter-spacing: 1.5px; }
  .card--back .brand__tag { font-size: 14px; letter-spacing: 21px; margin-top: 8px; }
</style>
</head>
<body>
  <section class="card card--front">
    <div class="accent-bar"></div>
    <div class="person">
      <p class="person__name">MARTIN OAKES</p>
      <p class="person__role">Managing Director</p>
    </div>
    <div class="feature-square"></div>
    <div class="brand">
      <span class="brand__square"></span>
      <div class="brand__text">
        <span class="brand__name">HALVENMOOR</span>
        <span class="brand__tag">CONSULTING</span>
      </div>
    </div>
    <div class="contact">
      <p class="contact__address">Your address, City<br>State, Zip 1234</p>
      <p class="contact__line">
        <svg viewBox="0 0 24 24"><path d="M6.6 10.8a15 15 0 0 0 6.6 6.6l2.2-2.2a1 1 0 0 1 1-.25 11.4 11.4 0 0 0 3.6.57 1 1 0 0 1 1 1V20a1 1 0 0 1-1 1A17 17 0 0 1 3 4a1 1 0 0 1 1-1h3.5a1 1 0 0 1 1 1c0 1.25.2 2.45.57 3.57a1 1 0 0 1-.25 1z"/></svg>
        123 456 789
      </p>
      <p class="contact__line">
        <svg viewBox="0 0 24 24"><path d="M2 5h20v14H2z M2 5l10 8 10-8" /></svg>
        info@halvenmoor.com
      </p>
      <p class="contact__line">
        <svg viewBox="0 0 24 24"><circle cx="12" cy="12" r="10"/></svg>
        www.halvenmoor.com
      </p>
    </div>
  </section>

  <section class="card card--back">
    <div class="brand">
      <span class="brand__square"></span>
      <div class="brand__text">
        <span class="brand__name">HALVENMOOR</span>
        <span class="brand__tag">CONSULTING</span>
      </div>
    </div>
  </section>
</body>
</html>
```